Design letter head and business card

Hello,

you should design a business card and letter paper for Kranichflug Marketing. In German we write this word with K insteat of C.

Company does not have a logo. But in general, we write Kranichflug Marketing in 2 lines.
First line red: KRANICHFLUG
Second line gray: MARKETING

Red (or wine red) and Gray / Black are our favorite colors.

Company slogan: "Fresh Ground Online Marketing".

Company offers SEO, SEM, SEA, AdWords, Conversion Optimization, Online Markting Consulting ...

The website is old, please do not use this as base for your task.

German letter paper sizes:
Viawable Dimensions : 210 x 297 mm
Needed file dimensions: 212 x 299 mm

Informations to include:

Address:
Kranichflug Marketing GmbH
Lindenweg 23
71599 Holderstadt
Germany

Geschäftsführer | CEO: Bernhard Olzner

Phone: +49 (0) 7388 846 27 05

Fax: +49 (0) 7388 846 27 88

Mail: info@kranichflug-beispiel.de

Web: www.kranichflug-beispiel.de

Amtsgericht Suttgart, HRB 537264

Bank: Rosenauer Bank
IBAN: DE827315480900XXXXXXXX
BIC: GENODES1RSQ

Thanks

Bernhard

Target Market(s)

People who likes to win the online marketing game.

Industry/Entity Type

Business

Contact Information for Business Card

Here is the personal text on the card:

Name:
Bernhard Olzner

Title:
Geschäftsführer | CEO

Address:
Kranichflug Marketing GmbH
Lindenweg 23
71599 Holderstadt
Germany

Phone:
+49 (0) 7388 846 27 05

Fax:
+49 (0) 7388 846 27 88

Mail:
olzner@kranichflug-beispiel.de

Web:
www.kranichflug-beispiel.de

Business Card:
Viewable Dimensions: 85 x 55 mm
Needed file dimensions: 87 x 57mm

Font styles to use
Sans Serif

Requirements
Nice to have
• It would be great to see the dynamics of a helicopter.

```html
<!DOCTYPE html>
<html lang="de">
<head>
<meta charset="utf-8">
<title>Kranichflug Marketing – Visitenkarte</title>
<link rel="stylesheet" href="https://fonts.googleapis.com/css2?family=Oswald:wght@600&family=Pathway+Gothic+One&display=swap">
<style>
  :root {
    --wine: #8e1f24;
    --paper: #e4e4e6;
    --ink: #2b2b2b;
    --ink-soft: #3a3a3a;
    --on-wine: #f4ecec;
    --stage: #ffffff;
  }
  * { margin: 0; padding: 0; box-sizing: border-box; }
  html, body { width: 1200px; height: 1000px; overflow: hidden; background: var(--stage); }
  body { position: relative; font-family: "Pathway Gothic One", "Arial Narrow", sans-serif; color: var(--ink); }

  .card {
    position: absolute;
    width: 840px;
    height: 440px;
    display: flex;
    overflow: hidden;
    box-shadow: 0 2px 6px rgba(0,0,0,.25);
  }
  .card--back { left: 330px; top: 30px; }
  .card--front { left: 30px; top: 525px; }

  .card__light { background: var(--paper); position: relative; }
  .card__wine { background: var(--wine); position: relative; flex: 1; color: var(--on-wine); }
  .card--back .card__light { width: 470px; }
  .card--front .card__light { width: 440px; }

  /* back side */
  .person { position: absolute; left: 50px; top: 140px; }
  .person__name { font-family: "Oswald", "Arial Narrow", sans-serif; font-weight: 600; font-size: 29px; color: var(--wine); line-height: 1.2; }
  .person__title { font-size: 27px; color: var(--ink-soft); line-height: 1.2; }
  .contact { position: absolute; left: 40px; top: 312px; list-style: none; font-size: 27px; line-height: 1.32; color: var(--ink); }

  .brand-small { position: absolute; right: 34px; top: 128px; text-align: right; }
  .brand-small__name { font-family: "Oswald", "Arial Narrow", sans-serif; font-weight: 600; font-size: 24px; line-height: 1.02; color: var(--paper); letter-spacing: .5px; }
  .brand-small__slogan { font-size: 14px; margin-top: 4px; color: var(--on-wine); }
  .address { position: absolute; right: 34px; top: 336px; text-align: right; font-style: normal; font-size: 26px; line-height: 1.38; }

  /* front side */
  .brand-large { position: absolute; left: 84px; top: 238px; }
  .brand-large__name { font-family: "Oswald", "Arial Narrow", sans-serif; font-weight: 600; font-size: 58px; line-height: 1.02; color: var(--ink); letter-spacing: 1px; }
  .brand-large__slogan { font-size: 30px; color: var(--ink); margin-top: 10px; }
  .website { position: absolute; left: 80px; top: 330px; font-family: "Oswald", "Arial Narrow", sans-serif; font-weight: 600; font-size: 22px; color: var(--on-wine); }
</style>
</head>
<body>

<section class="card card--back" aria-label="Rückseite der Visitenkarte">
  <div class="card__light">
    <div class="person">
      <p class="person__name">Bernhard Olzner</p>
      <p class="person__title">Geschäftsführer | CEO</p>
    </div>
    <ul class="contact">
      <li>Phone: +49 (0) 7388 846 27 05</li>
      <li>Fax: +49 (0) 7388 846 27 88</li>
      <li>E-mail: info@kranichflug-beispiel.de</li>
    </ul>
  </div>
  <div class="card__wine">
    <div class="brand-small">
      <p class="brand-small__name">KRANICHFLUG<br>MARKETING</p>
      <p class="brand-small__slogan">Fresh Ground Online Marketing</p>
    </div>
    <address class="address">
      Kranichflug Marketing GmbH,<br>
      Lindenweg 23,<br>
      71599 Holderstadt, Germany
    </address>
  </div>
</section>

<section class="card card--front" aria-label="Vorderseite der Visitenkarte">
  <div class="card__light">
    <div class="brand-large">
      <p class="brand-large__name">KRANICHFLUG<br>MARKETING</p>
      <p class="brand-large__slogan">Fresh Ground Online Marketing</p>
    </div>
  </div>
  <div class="card__wine">
    <p class="website">www.kranichflug-beispiel.de</p>
  </div>
</section>

</body>
</html>
```